Marbrook Cupcakes Website

We need a new website. We make Texas-size gourmet cupcakes and cupcake jars. We want a website similar to the one KEYlane is hosting and made. They're charging too much per month. I would like to have Blu Otter host it. see the current site at: marbrookcupcakes.com

```html
<!DOCTYPE html>
<html lang="en">
<head>
<meta charset="utf-8">
<title>Marbrook Cupcakes</title>
<link href="https://fonts.googleapis.com/css2?family=Poppins:wght@300;400;500;600;700&family=Lora:ital@1&display=swap" rel="stylesheet">
<style>
:root{
  --teal:#1fb1b6;
  --teal-light:#d3f3f3;
  --brown:#2f170b;
  --brown-footer:#3b1d0f;
  --ink:#2b2b2b;
  --beige:#efebe4;
  --white:#ffffff;
  --star:#f29a1f;
}
*{margin:0;padding:0;box-sizing:border-box}
html,body{width:1200px;height:4399px;overflow:hidden}
body{position:relative;background:var(--white);font-family:"Poppins",sans-serif;color:var(--ink)}

/* header */
.site-header{position:absolute;left:0;top:0;width:1200px;height:75px;background:var(--white);overflow:hidden}
.brand{position:absolute;left:96px;top:22px;font-weight:700;font-size:20px;color:var(--brown);letter-spacing:.2px}
.main-nav a{position:absolute;top:29px;transform:translateX(-50%);font-size:13px;font-weight:600;color:#333;text-decoration:none;white-space:nowrap}
.nav-marker{position:absolute;left:360px;top:-22px;width:34px;height:34px;border-radius:50%;background:var(--teal)}

/* hero */
.hero{position:absolute;left:0;top:75px;width:1200px;height:650px;background:radial-gradient(ellipse at 66% 35%,#6b3a22 0%,#3f2416 38%,#221510 70%,#1a120e 100%)}
.hero-kicker{position:absolute;left:114px;top:216px;color:#fff;font-size:19px;letter-spacing:4px}
.hero-title{position:absolute;left:112px;top:248px;color:#fff;font-size:56px;font-weight:400;line-height:54px}
.btn{display:inline-flex;align-items:center;justify-content:center;background:var(--teal);color:#fff;font-weight:700;border-radius:30px;letter-spacing:1.2px;text-decoration:none}
.hero-btn{position:absolute;left:113px;top:380px;width:175px;height:45px;font-size:14px}
.hero-arrow{position:absolute;top:275px}
.torn{position:absolute;left:0;width:1200px}

/* section titles */
.section-title{position:absolute;font-size:37px;font-weight:300;color:var(--ink);white-space:nowrap;z-index:1}
.section-title.centered{left:0;width:1200px;text-align:center}
.section-title b{font-weight:600}
.accent{position:relative;display:inline-block}
.accent::before{content:"";position:absolute;left:50%;top:50%;width:48px;height:48px;border-radius:50%;background:var(--teal);transform:translate(-30%,-50%);z-index:-1}

/* cupcake cards */
.cupcake-card{position:absolute;width:491px;height:324px;background:var(--beige);border-radius:8px;overflow:hidden;box-shadow:0 2px 8px rgba(0,0,0,.08)}
.cupcake-card svg{position:absolute;right:0;top:0}
.card-title{position:absolute;left:49px;top:80px;font-size:31px;font-weight:400;color:#3a3a3a}
.card-text{position:absolute;left:53px;top:128px;width:210px;font-size:10.5px;line-height:21px;color:#555}
.card-btn{position:absolute;left:48px;top:200px;width:138px;height:35px;font-size:11px}

/* story */
.story{position:absolute;left:0;top:1656px;width:1200px;height:530px}
.story-panel{position:absolute;left:0;top:0;width:617px;height:530px;background:var(--brown)}
.story-photo{position:absolute;left:617px;top:0;width:583px;height:530px;background:radial-gradient(ellipse at 55% 55%,#f1e7d8 0%,#d9c3a6 30%,#9a5a34 60%,#5d2c17 100%)}
.story .section-title{color:#fff;left:213px;top:111px}
.story-text{position:absolute;left:100px;top:185px;width:472px;text-align:center;color:#fff;font-size:17px;font-weight:300;line-height:29px}
.outline-btn{position:absolute;left:246px;top:391px;width:180px;height:48px;border:2px solid var(--teal);border-radius:26px;color:var(--teal);display:flex;align-items:center;justify-content:center;font-size:14px;letter-spacing:2px}

/* jars */
.jar-card{position:absolute;top:2325px;width:263px;height:372px;background:var(--teal-light);border-radius:132px 132px 0 0}
.jar-card.is-active{background:var(--teal)}
.jar-photo{position:absolute;left:22px;top:23px;width:219px;height:219px;border-radius:50%;background:radial-gradient(circle at 45% 60%,#d9b07a 0%,#8c5c34 45%,#3a2418 100%)}
.jar-card.blue .jar-photo{background:radial-gradient(circle at 45% 55%,#2bb4d8 0%,#5d3a26 55%,#2a1a12 100%)}
.jar-title{position:absolute;left:0;width:100%;top:255px;text-align:center;font-size:27px;font-weight:300;color:#333}
.jar-text{position:absolute;left:30px;width:203px;top:301px;text-align:center;font-size:11px;line-height:21px;color:#555}
.jar-card.is-active .jar-title,.jar-card.is-active .jar-text{color:#fff}
.dots span{position:absolute;height:2px;width:44px}

/* reviews */
.reviews{position:absolute;left:0;top:2800px;width:1200px;height:520px;background:radial-gradient(ellipse at 20% 20%,#3dc4c6 0%,#22aeb2 40%,#179ea3 100%)}
.reviews .section-title{color:#fff;left:428px;top:45px}
.reviews .accent::before{background:var(--brown)}
.review-card{position:absolute;background:#fff;text-align:center;box-shadow:0 4px 14px rgba(0,0,0,.12)}
.review-card.featured{border:2px solid #e7e7e7}
.stars{color:var(--star);font-size:21px;letter-spacing:3px}
.quote{font-family:"Lora",serif;font-style:italic;font-size:14px;line-height:24px;color:#444;margin-top:10px}
.reviewer{font-size:13px;font-weight:600;color:#222;margin-top:14px}

/* recipes */
.recipe-feature{position:absolute;left:119px;top:3464px;width:427px;height:348px;overflow:hidden}
.recipe-feature .photo{position:absolute;left:0;top:0;width:427px;height:235px;background:radial-gradient(ellipse at 50% 45%,#f6f1ea 0%,#e6d3c7 35%,#b7352f 55%,#6a2a1c 100%)}
.recipe-feature .caption{position:absolute;left:0;top:235px;width:427px;height:113px;background:#3e1d0c}
.caption p{position:absolute;left:28px;top:30px;width:370px;color:#fff;font-size:14.5px;line-height:22px}
.link{font-size:10px;font-weight:600;text-decoration:underline}
.caption .link{position:absolute;left:28px;top:84px;color:#fff}
.recipe-card{position:absolute;top:3464px;width:249px;height:345px;border:1px solid #ddd;background:#fff}
.recipe-card .photo{height:181px}
.recipe-card h3{margin:20px 0 0 28px;width:200px;font-size:12.5px;line-height:15px;font-weight:600;color:#222}
.recipe-card .rule{margin:6px 0 0 28px;width:30px;height:2px;background:#1e4f9c}
.recipe-card p{margin:8px 0 0 28px;width:205px;font-size:8px;line-height:11px;color:#777}
.recipe-card .link{display:block;margin:14px 0 0 28px;color:#222}

/* social strip */
.social-strip{position:absolute;left:0;top:3969px;width:1200px;height:210px;display:flex}
.social-strip div{flex:1}

/* footer */
.site-footer{position:absolute;left:0;top:4179px;width:1200px;height:220px;background:var(--brown-footer);color:#fff}
.footer-nav a{position:absolute;top:55px;transform:translateX(-50%);color:#fff;text-decoration:none;font-size:14px;font-weight:600;white-space:nowrap}
.copyright{position:absolute;left:0;width:1200px;top:99px;text-align:center;font-size:13px}
.social{position:absolute;top:148px;width:24px;height:24px;border-radius:50%;background:var(--teal)}
</style>
</head>
<body>

<header class="site-header">
  <div class="brand">MARBROOK CUPCAKES</div>
  <span class="nav-marker"></span>
  <nav class="main-nav">
    <a style="left:377px">HOME</a>
    <a style="left:490px">OUR STORY</a>
    <a style="left:638px">OUR CUP CAKES</a>
    <a style="left:778px">REVIEWS</a>
    <a style="left:886px">BLOGS</a>
    <a style="left:1007px">CONTACT US</a>
  </nav>
</header>

<section class="hero" role="img" aria-label="Chocolate cupcake with swirled frosting and sprinkles on a wooden board">
  <svg class="hero-arrow" style="left:43px" width="20" height="32" viewBox="0 0 20 32"><path d="M16 3 L4 16 L16 29" stroke="#fff" stroke-width="4" fill="none"/></svg>
  <svg class="hero-arrow" style="left:1130px" width="20" height="32" viewBox="0 0 20 32"><path d="M4 3 L16 16 L4 29" stroke="#fff" stroke-width="4" fill="none"/></svg>
  <div class="hero-kicker">WELCOME TO MARBROOK CUPCAKES</div>
  <h1 class="hero-title">TASTY MARBROOK<br>CUPCAKES</h1>
  <a class="btn hero-btn">TRY IT NOW</a>
</section>
<svg class="torn" style="top:700px" height="30" viewBox="0 0 1200 30" preserveAspectRatio="none"><path d="M0 14 L40 10 L80 16 L130 9 L170 15 L220 11 L270 17 L320 10 L370 14 L420 8 L470 15 L520 11 L570 16 L620 9 L670 14 L720 10 L770 17 L820 11 L870 15 L920 9 L970 16 L1020 10 L1070 15 L1120 11 L1170 16 L1200 12 L1200 30 L0 30Z" fill="#fff"/></svg>

<h2 class="section-title" style="left:452px;top:795px">OUR <b>CUPCAK<span class="accent">ES</span></b></h2>

<article class="cupcake-card" style="left:111px;top:900px">
  <svg width="250" height="324" viewBox="0 0 250 324" role="img" aria-label="Assorted frosted cupcakes in branded cups"><defs><linearGradient id="g1" x1="0" x2="1"><stop offset="0" stop-color="#8a4a2a"/><stop offset=".5" stop-color="#e7d6c1"/><stop offset="1" stop-color="#7a3f2a"/></linearGradient></defs><path d="M38 0 H250 V324 H24 C0 250 40 170 28 110 C20 60 36 20 38 0Z" fill="url(#g1)"/></svg>
  <div class="card-title">Cupcake Title</div>
  <p class="card-text">Lorem ipsum dolor sit amet, consectetur adipiscing elit, sed do eiusmod tempor incididunt ut labore</p>
  <a class="btn card-btn">SHOP NOW</a>
</article>
<article class="cupcake-card" style="left:630px;top:899px">
  <svg width="250" height="324" viewBox="0 0 250 324" role="img" aria-label="Vanilla, cookie and strawberry cupcakes in a tray"><defs><linearGradient id="g2" x1="0" x2="1" y1="0" y2="1"><stop offset="0" stop-color="#f1ede6"/><stop offset=".55" stop-color="#5b4a3e"/><stop offset="1" stop-color="#e88aa3"/></linearGradient></defs><path d="M38 0 H250 V324 H24 C0 250 40 170 28 110 C20 60 36 20 38 0Z" fill="url(#g2)"/></svg>
  <div class="card-title">Cupcake Title</div>
  <p class="card-text">Lorem ipsum dolor sit amet, consectetur adipiscing elit, sed do eiusmod tempor incididunt ut labore</p>
  <a class="btn card-btn">SHOP NOW</a>
</article>
<article class="cupcake-card" style="left:113px;top:1251px">
  <svg width="250" height="324" viewBox="0 0 250 324" role="img" aria-label="Chocolate cupcake with white frosting and sprinkles"><defs><radialGradient id="g3" cx=".6" cy=".55"><stop offset="0" stop-color="#f5f1ec"/><stop offset=".55" stop-color="#e8e2dc"/><stop offset="1" stop-color="#4a2a1c"/></radialGradient></defs><path d="M30 0 H250 V324 H10 C0 250 10 150 20 80 C24 40 28 20 30 0Z" fill="url(#g3)"/></svg>
  <div class="card-title">Cupcake Title</div>
  <p class="card-text">Lorem ipsum dolor sit amet, consectetur adipiscing elit, sed do eiusmod tempor incididunt ut labore</p>
  <a class="btn card-btn">SHOP NOW</a>
</article>
<article class="cupcake-card" style="left:631px;top:1250px">
  <svg width="250" height="324" viewBox="0 0 250 324" role="img" aria-label="Box of assorted gourmet cupcakes on pink"><defs><linearGradient id="g4" x1="0" x2="1" y1="0" y2="1"><stop offset="0" stop-color="#d6497f"/><stop offset=".4" stop-color="#ecdcc6"/><stop offset="1" stop-color="#8a5a3a"/></linearGradient></defs><path d="M38 0 H250 V324 H24 C0 250 40 170 28 110 C20 60 36 20 38 0Z" fill="url(#g4)"/></svg>
  <div class="card-title">Cupcake Title</div>
  <p class="card-text">Lorem ipsum dolor sit amet, consectetur adipiscing elit, sed do eiusmod tempor incididunt ut labore</p>
  <a class="btn card-btn">SHOP NOW</a>
</article>

<section class="story">
  <div class="story-panel"></div>
  <div class="story-photo" role="img" aria-label="Close-up of a cupcake with cream frosting and toffee crumble"></div>
  <h2 class="section-title">OUR <b>STO<span class="accent">RY</span></b></h2>
  <p class="story-text">Lorem ipsum dolor sit amet, consectetur adipiscing elit, sed do eiusmod tempor incididunt ut labore et dolore magna aliqua. Ut enim ad minim veniam, quis nostrud exercitation ullamco laboris nisi ut aliquip ex ea commodo consequat. Duis aute irure dolor in reprehenderit in voluptate velit esse cillum dolo</p>
  <a class="outline-btn">LEARN MORE</a>
</section>
<svg class="torn" style="top:2170px" height="24" viewBox="0 0 1200 24" preserveAspectRatio="none"><path d="M0 10 L50 6 L100 12 L150 5 L200 11 L260 7 L310 13 L360 6 L420 11 L470 5 L530 12 L580 7 L640 12 L690 6 L750 11 L800 5 L860 12 L910 7 L970 12 L1020 6 L1080 11 L1130 7 L1200 11 L1200 24 L0 24Z" fill="#fff"/></svg>

<h2 class="section-title" style="left:447px;top:2247px">OUR <b>CUPCAKE JA<span class="accent">RS</span></b></h2>

<article class="jar-card blue" style="left:174px">
  <div class="jar-photo" role="img" aria-label="Two layered cupcake jars with blue lids"></div>
  <div class="jar-title">Cupcake Jar</div>
  <p class="jar-text">Lorem ipsum dolor sit amet, consectetur adipiscing elit, se</p>
</article>
<article class="jar-card blue is-active" style="left:476px">
  <div class="jar-photo" role="img" aria-label="Two chocolate cupcake jars with blue lids"></div>
  <div class="jar-title">Cupcake Jar</div>
  <p class="jar-text">Lorem ipsum dolor sit amet, consectetur adipiscing elit, se</p>
</article>
<article class="jar-card" style="left:777px">
  <div class="jar-photo" role="img" aria-label="Two open cupcake jars with crumble topping"></div>
  <div class="jar-title">Cupcake Jar</div>
  <p class="jar-text">Lorem ipsum dolor sit amet, consectetur adipiscing elit, se</p>
</article>
<div class="dots">
  <span style="left:516px;top:2739px;background:#333"></span>
  <span style="left:576px;top:2739px;background:var(--teal-light)"></span>
  <span style="left:634px;top:2739px;background:var(--teal-light)"></span>
</div>

<section class="reviews">
  <h2 class="section-title">CUSTOMER <b>REVI<span class="accent">EWS</span></b></h2>
  <div class="review-card" style="left:67px;top:155px;width:331px;height:227px;padding:28px 22px 0">
    <div class="stars">★★★★★</div>
    <p class="quote">“Lorem ipsum dolor sit amet, consectetur adipiscing elit, sed do eiusmod tempor incididunt ut labore et dolore magna aliqua”</p>
    <div class="reviewer">Customer Name</div>
  </div>
  <div class="review-card featured" style="left:420px;top:128px;width:331px;height:295px;padding:32px 26px 0">
    <div class="stars">★★★★★</div>
    <p class="quote">“Lorem ipsum dolor sit amet, consectetur adipiscing elit, sed do eiusmod tempor incididunt ut labore et dolore ipsum dolor sit amet, consectetur adipiscing elit, sed do eiusmod tempor incididunt ut labore et dolore magna aliqua”</p>
    <div class="reviewer">Customer Name</div>
  </div>
  <div class="review-card" style="left:778px;top:155px;width:332px;height:227px;padding:28px 22px 0">
    <div class="stars">★★★★★</div>
    <p class="quote">“Lorem ipsum dolor sit amet, consectetur adipiscing elit, sed do eiusmod tempor incididunt ut labore et dolore magna aliqua”</p>
    <div class="reviewer">Customer Name</div>
  </div>
  <div class="dots">
    <span style="left:525px;top:469px;background:#fff;width:40px"></span>
    <span style="left:570px;top:469px;background:#222;width:40px"></span>
    <span style="left:616px;top:469px;background:#222;width:40px"></span>
  </div>
</section>
<svg class="torn" style="top:3300px" height="24" viewBox="0 0 1200 24" preserveAspectRatio="none"><path d="M0 9 L60 13 L110 6 L170 12 L220 7 L280 13 L330 6 L390 11 L440 5 L500 12 L550 8 L610 13 L660 6 L720 11 L770 5 L830 12 L880 7 L940 13 L990 6 L1050 11 L1100 5 L1160 12 L1200 8 L1200 24 L0 24Z" fill="#fff"/></svg>

<h2 class="section-title" style="left:118px;top:3384px">LATEST <b>RECIP<span class="accent">ES</span></b></h2>

<article class="recipe-feature">
  <div class="photo" role="img" aria-label="Red velvet cupcake topped with white frosting and red crumbs"></div>
  <div class="caption">
    <p>Sed ut perspiciatis unde omnis iste natus error sit voluptatem accusantium doloremqu</p>
    <span class="link">LEARN MORE</span>
  </div>
</article>
<article class="recipe-card" style="left:567px">
  <div class="photo" role="img" aria-label="Cookies and cream cupcake with chocolate crumbs" style="background:radial-gradient(ellipse at 50% 45%,#6b5548 0%,#2d201b 55%,#a2643a 100%)"></div>
  <h3>Lorem ipsum dolor sit amet, consectetur adipiscing elit</h3>
  <div class="rule"></div>
  <p>Lorem ipsum dolor sit amet consectetuer adipiscing elit Nam cursus Morbi ut mi Nullam enim leo egestas id condimentum at laoreet mattis massa egestas</p>
  <span class="link">LEARN MORE</span>
</article>
<article class="recipe-card" style="left:831px">
  <div class="photo" role="img" aria-label="Strawberry cupcake with pink frosting" style="background:radial-gradient(ellipse at 50% 40%,#d8353a 0%,#f2c8c8 35%,#f4e6de 60%,#b06a3c 100%)"></div>
  <h3>Lorem ipsum dolor sit amet, consectetur adipiscing elit</h3>
  <div class="rule"></div>
  <p>Lorem ipsum dolor sit amet consectetuer adipiscing elit Nam cursus Morbi ut mi Nullam enim leo egestas id condimentum at laoreet mattis massa egestas</p>
  <span class="link">LEARN MORE</span>
</article>

<h2 class="section-title centered" style="top:3894px">FIND US ON <b>SOCI<span class="accent">AL</span></b></h2>

<div class="social-strip">
  <div role="img" aria-label="Cupcake with crumble topping" style="background:radial-gradient(ellipse at 50% 40%,#e7c89a 0%,#b98550 55%,#6a4a30 100%)"></div>
  <div role="img" aria-label="Cupcakes with orange frosting" style="background:radial-gradient(ellipse at 50% 50%,#f07b2a 0%,#b8542a 45%,#5a2a18 100%)"></div>
  <div role="img" aria-label="White frosted cupcakes, dimmed" style="background:radial-gradient(ellipse at 50% 50%,#6a6460 0%,#3f3a37 60%,#2a2624 100%)"></div>
  <div role="img" aria-label="Cupcakes in a display case" style="background:linear-gradient(180deg,#2a2220 0%,#4a3a30 45%,#d8c29e 70%,#3a2e28 100%)"></div>
  <div role="img" aria-label="Chocolate cupcake with vanilla swirl" style="background:radial-gradient(ellipse at 50% 40%,#f3eee6 0%,#d8cec2 45%,#4a2e22 100%)"></div>
</div>

<footer class="site-footer">
  <nav class="footer-nav">
    <a style="left:270px">OUR STORY</a>
    <a style="left:432px">OUR CUP CAKES</a>
    <a style="left:580px">WHY US</a>
    <a style="left:702px">REVIEWS</a>
    <a style="left:818px">BLOGS</a>
    <a style="left:951px">CONTACT US</a>
  </nav>
  <p class="copyright">© 2025 Company Name | All Rights Reserved</p>
  <span class="social" style="left:518px" aria-label="Social link"></span>
  <span class="social" style="left:570px" aria-label="Social link"></span>
  <span class="social" style="left:622px" aria-label="Social link"></span>
  <span class="social" style="left:674px" aria-label="Social link"></span>
</footer>

</body>
</html>
```